Computer Company needs a Business card design

We need a business card design for our business. We assist people to transition to the KVS (Kestrel Vantage Scheme). The Verandal Crown Office-owned kvs™ network is a brand new telecommunications network currently being rolled out across Australia, giving access to a reliable broadband connection. Our niche market will predominantly be domestic customers in the 50+ age bracket. The assistance that we provide is everything from arranging the equipment, arranging the plan and contract term, appointment times, final testing of the network and any tweaks that need to be made. We basically PM the transition from start to finish. The business card design should be minimalist, should communicate loyalty and stability, should be easy to read and clearly explain what we do. We have asked for front and back. However, the back of the card does not have to include much information at all. It could be just a small design, or a repeat of our phone number. Up to you. The attached file only says what is required on the card. It does not specify where to arrange the text, what fonts to use, etc etc. As much as we would like to give you more info, due to our very limited design ability, we are not really able to send you any rough, or otherwise, designs of what we are after. Hopefully the above description is enough for you.

```html
<!DOCTYPE html>
<html lang="en">
<head>
<meta charset="utf-8">
<title>KVS Connect – Business Card</title>
<link href="https://fonts.googleapis.com/css2?family=Roboto:wght@300;400;700&display=swap" rel="stylesheet">
<style>
  :root {
    --backdrop: #1f1f1f;
    --card: #050505;
    --blue: #13a6e6;
    --white: #ffffff;
    --muted: #d9d9d9;
  }
  html, body {
    margin: 0;
    width: 1200px;
    height: 930px;
    overflow: hidden;
    background: var(--backdrop);
    font-family: "Roboto", Arial, sans-serif;
  }
  .canvas {
    position: relative;
    width: 1200px;
    height: 930px;
  }
  .card {
    position: absolute;
    width: 620px;
    height: 360px;
    background: var(--card);
    overflow: hidden;
    box-shadow: 0 12px 30px rgba(0,0,0,0.5);
  }
  .card--back { left: 90px; top: 70px; }
  .card--front { left: 490px; top: 490px; }

  .wordmark {
    position: absolute;
    margin: 0;
    font-weight: 700;
    font-size: 60px;
    letter-spacing: 3px;
    color: var(--white);
    line-height: 1;
    white-space: nowrap;
  }
  .card--back .wordmark { left: 0; right: 0; top: 150px; text-align: center; }
  .card--front .wordmark { left: 40px; top: 58px; font-size: 50px; }

  .holder {
    position: absolute;
    right: 34px;
    top: 150px;
    text-align: right;
  }
  .holder__name {
    font-size: 26px;
    font-weight: 400;
    color: var(--blue);
    margin: 0;
  }
  .holder__role {
    font-size: 15px;
    font-weight: 300;
    color: var(--muted);
    margin: 2px 0 0;
  }
  .rule {
    position: absolute;
    left: 30px;
    right: 34px;
    top: 210px;
    height: 1px;
    background: var(--blue);
  }
  .contact {
    position: absolute;
    left: 34px;
    top: 228px;
    margin: 0;
    padding: 0;
    list-style: none;
  }
  .contact__item {
    display: flex;
    align-items: center;
    gap: 10px;
    font-size: 17px;
    font-weight: 300;
    color: var(--white);
    line-height: 26px;
  }
  .contact__icon { width: 12px; height: 12px; }
  .base-band {
    position: absolute;
    left: 0;
    right: 0;
    bottom: 0;
    height: 14px;
    display: flex;
  }
  .base-band__light { flex: 0 0 55%; background: var(--white); }
  .base-band__accent { flex: 1; background: var(--blue); }
</style>
</head>
<body>
<main class="canvas">
  <section class="card card--back" aria-label="Card back">
    <p class="wordmark">KVS CONNECT</p>
  </section>

  <section class="card card--front" aria-label="Card front">
    <p class="wordmark">KVS CONNECT</p>

    <div class="holder">
      <p class="holder__name">Owen Farrady</p>
      <p class="holder__role">Director</p>
    </div>

    <div class="rule"></div>

    <ul class="contact">
      <li class="contact__item">
        <svg class="contact__icon" viewBox="0 0 12 12"><path d="M2.5 1 L4.5 1 L5 3.5 L3.8 4.5 Q5 7 7.5 8.2 L8.5 7 L11 7.5 L11 9.5 Q11 11 9.5 11 Q1 10 1 2.5 Q1 1 2.5 1Z" fill="var(--blue)"/></svg>
        0491570156
      </li>
      <li class="contact__item">
        <svg class="contact__icon" viewBox="0 0 12 12"><rect x="1" y="2.5" width="10" height="7" fill="none" stroke="var(--blue)" stroke-width="1.2"/><path d="M1 2.5 L6 6.5 L11 2.5" fill="none" stroke="var(--blue)" stroke-width="1.2"/></svg>
        info@kvsconnect.com.au
      </li>
      <li class="contact__item">
        <svg class="contact__icon" viewBox="0 0 12 12"><circle cx="6" cy="6" r="5" fill="none" stroke="var(--blue)" stroke-width="1.1"/><ellipse cx="6" cy="6" rx="2.2" ry="5" fill="none" stroke="var(--blue)" stroke-width="1"/><path d="M1 6 H11" stroke="var(--blue)" stroke-width="1"/></svg>
        www.kvsconnect.com.au
      </li>
    </ul>

    <div class="base-band">
      <span class="base-band__light"></span>
      <span class="base-band__accent"></span>
    </div>
  </section>
</main>
</body>
</html>
```